Business Card Design For A Renovation Contractor Company

We need a business card for a new company based in Singapore, our company name is "RB Tolvane". We are a renovation contractor that builds designs into reality. We build more of F&B restaurants, retail stores and commercial offices. We work very closely with designers. The final design should communicate to our client that we are a company that you can trust, that will plan and complete your project without giving you a headache. I like my client to remember my company as "RB". The beauty of SIMPLE is important.

Industry/Entity Type

Contractor

Requirements
Nice to have
• Black or Red base

```html
<!DOCTYPE html>
<html lang="en">
<head>
<meta charset="utf-8">
<title>RB Tolvane – Business Card</title>
<link rel="stylesheet" href="https://fonts.googleapis.com/css2?family=Lato:wght@400;700&display=swap">
<style>
  :root {
    --stage: #e9e7e4;
    --brand-red: #c0161f;
    --ink: #2b2626;
    --paper: #f2f2f2;
    --shadow: rgba(0, 0, 0, 0.18);
  }
  * { box-sizing: border-box; margin: 0; padding: 0; }
  html, body {
    width: 1200px; height: 900px; overflow: hidden;
    background: var(--stage);
    font-family: "Lato", Arial, sans-serif;
    color: var(--ink);
  }
  .card-set {
    position: absolute; inset: 0;
    display: flex; align-items: center; justify-content: center; gap: 48px;
  }
  .card {
    position: relative;
    width: 518px; height: 296px;
    box-shadow: 0 10px 28px var(--shadow);
  }
  /* Front */
  .card--front {
    background: var(--brand-red);
    display: flex; flex-direction: column; align-items: center; justify-content: center;
  }
  .front-mark {
    display: flex; align-items: center; gap: 14px;
    font-size: 40px; font-weight: 700; color: var(--ink); letter-spacing: 0.5px;
  }
  .mark-dot {
    width: 22px; height: 22px; border-radius: 50%; background: var(--ink);
  }
  .front-web {
    margin-top: 34px; font-size: 14px; letter-spacing: 1.5px; color: var(--ink);
  }
  /* Back */
  .card--back { background: var(--paper); }
  .brand {
    position: absolute; top: 40px; right: 36px;
  }
  .brand-name {
    font-size: 30px; font-weight: 400; color: var(--brand-red); line-height: 1;
  }
  .contact { position: absolute; left: 40px; bottom: 38px; }
  .person {
    position: relative; padding-left: 18px;
    font-size: 20px; color: var(--ink);
  }
  .person::before {
    content: ""; position: absolute; left: 0; top: 8px;
    width: 2px; height: 12px; background: var(--brand-red);
  }
  .person-role { font-size: 13px; letter-spacing: 0.5px; margin-left: 4px; }
  .details {
    position: relative; margin-top: 14px; padding-left: 18px;
    font-size: 14px; line-height: 1.5;
  }
  .details::before {
    content: ""; position: absolute; left: 0; top: 30px;
    width: 2px; height: 58px; background: var(--brand-red);
  }
  .detail-label { display: inline-block; width: 18px; }
</style>
</head>
<body>
  <main class="card-set">
    <section class="card card--front" aria-label="Card front">
      <div class="front-mark"><span class="mark-dot"></span>RB Tolvane</div>
      <p class="front-web">www.rbtolvane.com</p>
    </section>

    <section class="card card--back" aria-label="Card back">
      <div class="brand">
        <p class="brand-name">RB Tolvane</p>
      </div>
      <div class="contact">
        <p class="person">Marcus Lim.<span class="person-role">DIRECTOR</span></p>
        <div class="details">
          <p><span class="detail-label">T</span>642.587.1290</p>
          <p><span class="detail-label">E</span>marcus@rbtolvane.com</p>
          <p>8 Tanvale Road, #03-210 Tanvale Centre</p>
          <p>Singapore 438812</p>
        </div>
      </div>
    </section>
  </main>
</body>
</html>
```